New business card for a regional office of a US M&A company

We need business card for a finance company, office based in Hong Kong , our Head office is in US, our business is to Merge and acquires companies , the new office will be a regional office for the Asia Pacific region. We want to use the head office logo as attached ( but don't have to be exactly the same, can be a variation to it) as a base and then add Asia Pacific alongside the logo.
We would prefer to have be bilingual Eng + Chinese, although we don't really have Chinese company name .

Industry/Entity Type

Business

Contact Information for Business Card

Clara Jo Tsang
 

VP,
APAC M&A Operations
Orin Vantage Asia Pacific Limited
 
Unit 1407, K18
18 Tai Lok Shan Road, 
Hong Kong 
 
M: +852 6038 1742
T : +852 2836 4100
F : +852 2836 4177
VOIP: 4158
 
cjtsang@orinvantage.com

Font styles to use
Serif
Sans Serif

Colors

Designer to choose colors to be used in the design.

Requirements
Must have
• APAC Office

```html
<!DOCTYPE html>
<html lang="en">
<head>
<meta charset="utf-8">
<title>Orin Vantage Asia Pacific – Business Card</title>
<link href="https://fonts.googleapis.com/css2?family=Open+Sans:wght@400;600;700;800&display=swap" rel="stylesheet">
<style>
  :root {
    --backdrop: #3b3b3d;
    --card: #1f2022;
    --card-gloss: #3c3d41;
    --accent: #27a9d8;
    --ink: #ffffff;
    --mark: #f2f2f2;
  }
  * { margin: 0; padding: 0; box-sizing: border-box; }
  html, body { width: 799px; height: 1200px; overflow: hidden; }
  body {
    background: var(--backdrop);
    font-family: "Open Sans", sans-serif;
    position: relative;
  }
  .card {
    position: absolute;
    left: 80px;
    width: 640px;
    height: 366px;
    background: var(--card);
    border-radius: 3px;
    box-shadow: 0 8px 24px rgba(0,0,0,.35);
    overflow: hidden;
  }
  .card--front { top: 160px; }
  .card--back { top: 680px; }

  /* Front */
  .front-brand {
    position: absolute;
    inset: 0;
    display: flex;
    align-items: center;
    justify-content: center;
    gap: 18px;
  }
  .front-brand__square {
    width: 34px; height: 34px;
    background: var(--card-gloss);
  }
  .front-brand__name {
    font-weight: 800;
    font-size: 44px;
    letter-spacing: 1px;
    color: var(--card-gloss);
  }

  /* Back */
  .holder { position: absolute; left: 40px; top: 34px; }
  .holder__name { color: var(--accent); font-weight: 700; font-size: 22px; line-height: 1.2; }
  .holder__title { color: var(--ink); font-size: 13px; line-height: 1.35; margin-top: 4px; }

  .company {
    position: absolute; left: 40px; top: 148px;
    color: var(--accent); font-weight: 700; font-size: 17px;
  }
  .contacts {
    position: absolute; left: 40px; top: 180px;
    list-style: none; color: var(--ink); font-size: 14px; line-height: 20px;
  }
  .contacts li { display: flex; align-items: center; gap: 10px; }
  .contacts svg { width: 12px; height: 12px; fill: var(--accent); flex: none; }
  .contacts .no-icon { padding-left: 22px; margin-left: -22px; }
  .contacts .label { color: var(--accent); }

  .accent-band {
    position: absolute; left: 0; right: 0; bottom: 26px; height: 7px;
    background: var(--accent);
  }
  .back-brand {
    position: absolute; right: 44px; top: 96px;
    display: flex; flex-direction: column; align-items: flex-end; gap: 14px;
  }
  .back-brand__square { width: 130px; height: 130px; background: var(--mark); }
  .back-brand__name { color: var(--mark); font-weight: 700; font-size: 16px; letter-spacing: 1px; }
</style>
</head>
<body>

<section class="card card--front">
  <div class="front-brand">
    <span class="front-brand__square"></span>
    <span class="front-brand__name">ORIN VANTAGE</span>
  </div>
</section>

<section class="card card--back">
  <div class="holder">
    <div class="holder__name">Clara Jo Tsang</div>
    <div class="holder__title">Vice President,<br>APAC M&amp;A Operations</div>
  </div>

  <div class="company">Orin Vantage Asia Pacific Limited</div>

  <ul class="contacts">
    <li>
      <svg viewBox="0 0 12 12"><rect x="3" y="0" width="6" height="12" rx="1.2"/></svg>
      +852 6038 1742
    </li>
    <li>
      <svg viewBox="0 0 12 12"><path d="M2 1h3l1 3-1.6 1.2a7 7 0 0 0 2.4 2.4L8 6l3 1v3a1.5 1.5 0 0 1-1.5 1.5A9 9 0 0 1 .5 2.5 1.5 1.5 0 0 1 2 1z"/></svg>
      +852 2836 4100
    </li>
    <li>
      <svg viewBox="0 0 12 12"><rect x="3" y="0" width="6" height="4"/><rect x="0" y="4" width="12" height="6" rx="1"/><rect x="3" y="8" width="6" height="4"/></svg>
      +852 2836 4177,&nbsp;<span class="label">VOIP:</span>&nbsp;4158
    </li>
    <li>
      <svg viewBox="0 0 12 12"><path d="M0 2h12v8H0z M0 2l6 4.5L12 2" /></svg>
      cjtsang@orinvantage.com
    </li>
    <li class="no-icon">Unit 1407, K18 18 Tai Lok Shan Road, Hong Kong</li>
  </ul>

  <div class="accent-band"></div>

  <div class="back-brand">
    <span class="back-brand__square"></span>
    <span class="back-brand__name">ORIN VANTAGE</span>
  </div>
</section>

</body>
</html>
```